Business card por a urban DJ, up scale audience target

Need a sober design, modern, conservative colors but i can consider some options, y play rnb, hip hop, EDM and top40.

Business card for contact and personal info, double sided, use logo attrached please; im 42 so i need a card acording to my age an target audience.

Target Market(s)

Adult people, up scale audience

Industry/Entity Type

Music Download

Contact Information for Business Card

Cel (318) 4207265518 www.lumadrift.com

Requirements
Must have
• open mind
Nice to have
• open mind
Should not have
• DJ

```html
<!DOCTYPE html>
<html lang="en">
<head>
<meta charset="utf-8">
<title>Lumadrift Business Card</title>
<link href="https://fonts.googleapis.com/css2?family=Montserrat:wght@300;500;700&display=swap" rel="stylesheet">
<style>
  :root {
    --bg: #e9e7e3;
    --card-black: #1b1b1b;
    --card-black-soft: #262626;
    --panel-white: #ffffff;
    --accent-grey: #8e8e8e;
    --logo-grey: #3b3b3b;
    --text-light: #f2f2f2;
    --text-muted: #cfcfcf;
  }
  * { box-sizing: border-box; margin: 0; padding: 0; }
  html, body {
    width: 1200px; height: 950px; overflow: hidden;
    background: var(--bg);
    font-family: "Montserrat", sans-serif;
  }
  .sheet {
    width: 1200px; height: 950px;
    display: flex; flex-direction: column;
    align-items: center; justify-content: center; gap: 40px;
  }
  .card {
    position: relative;
    width: 700px; height: 400px;
    background: linear-gradient(135deg, var(--card-black-soft), var(--card-black));
    overflow: hidden;
    box-shadow: 0 6px 18px rgba(0,0,0,.18);
  }
  .card__art { position: absolute; inset: 0; }
  .brand {
    position: absolute; left: 0; top: 110px; width: 290px; height: 290px;
    display: flex; align-items: center; justify-content: center;
  }
  .brand__name {
    font-weight: 700; font-size: 34px; letter-spacing: 2px;
    color: var(--logo-grey);
  }
  .contact {
    position: absolute; left: 345px; top: 140px;
    color: var(--text-light);
  }
  .contact__name {
    font-weight: 500; font-size: 27px; letter-spacing: 1px;
  }
  .contact__role {
    font-weight: 300; font-size: 20px; margin-top: 4px; letter-spacing: .5px;
  }
  .contact__list { list-style: none; margin-top: 26px; }
  .contact__item {
    display: flex; align-items: center; gap: 12px;
    font-weight: 300; font-size: 18px; color: var(--text-muted);
    margin-bottom: 10px;
  }
  .contact__icon { width: 16px; height: 16px; flex: none; }
</style>
</head>
<body>
<main class="sheet">
  <section class="card card--front">
    <svg class="card__art" width="700" height="400" viewBox="0 0 700 400" aria-hidden="true">
      <rect x="0" y="110" width="290" height="290" fill="var(--panel-white)"/>
      <polygon points="160,110 290,110 290,0 245,0" fill="var(--accent-grey)"/>
      <line x1="150" y1="110" x2="238" y2="0" stroke="var(--panel-white)" stroke-width="4"/>
    </svg>
    <div class="brand"><span class="brand__name">LUMADRIFT</span></div>
    <div class="contact">
      <h1 class="contact__name">MARCUS VALE</h1>
      <p class="contact__role">CEO/FOUNDER</p>
      <ul class="contact__list">
        <li class="contact__item">
          <svg class="contact__icon" viewBox="0 0 16 16"><rect x="3" y="1" width="10" height="14" rx="1.5" fill="none" stroke="currentColor" stroke-width="1.4"/><circle cx="8" cy="12.5" r="0.9" fill="currentColor"/></svg>
          (318) 4207265518
        </li>
        <li class="contact__item">
          <svg class="contact__icon" viewBox="0 0 16 16"><circle cx="8" cy="8" r="6.5" fill="none" stroke="currentColor" stroke-width="1.4"/><ellipse cx="8" cy="8" rx="2.8" ry="6.5" fill="none" stroke="currentColor" stroke-width="1.1"/><line x1="1.5" y1="8" x2="14.5" y2="8" stroke="currentColor" stroke-width="1.1"/></svg>
          www.lumadrift.com
        </li>
      </ul>
    </div>
  </section>
  <section class="card card--back" aria-label="Card back"></section>
</main>
</body>
</html>
```